Website Design for WestaKolory.pl – Luxury Wedding Car Rental with Chauffeur

We are looking for a talented designer to create a modern, elegant, and fully responsive website for our new brand – WestyKolory.pl. We are a premium car rental platform in Poland, offering luxury and exotic vehicles exclusively for weddings. All cars come with a professional chauffeur, ensuring a high-end, stress-free, and stylish experience.
Website Purpose:
The website should present our offering in a luxurious, clear, and inspiring way. It must build trust, highlight the prestige of our brand, and encourage inquiries. Our target audience includes engaged couples, wedding planners, and clients seeking a truly exceptional vehicle for their special day.
Design Requirements:
Style: modern, elegant, minimalist
Color palette: white, black, gold, optionally silver – refined and luxurious
Typography: clean, modern, high-end
Layout: clear, intuitive, with large car images and well-defined sections
Fully responsive (desktop, tablet, mobile)
Bilingual layout (Polish/English) must be considered
Pages to Design:
Homepage
About Us
Fleet Overview
Individual Car Pages
Services (Weddings, Photo Shoots, Film Rentals)
Why Us / Unique Selling Points
Contact
FAQ
Inspiration:
Luxury automotive brands (e.g. Varnel-Hoske, Corvash, Elbrin Tusko)
High-end wedding websites
Minimalist layouts with large visuals and elegant typography
Additional Notes:
The design should evoke the emotions of a wedding day – elegance, uniqueness, style, and class. Please avoid flashy colors, excessive graphic effects, or overly decorative elements. Subtlety, prestige, and sophistication are key.

```html
<!DOCTYPE html>
<html lang="en">
<head>
<meta charset="utf-8">
<title>WestaKolory.pl – Luxury Car Wedding</title>
<link rel="stylesheet" href="https://fonts.googleapis.com/css2?family=Cinzel:wght@400;600;700&family=Poppins:wght@300;400;500;600;700&display=swap">
<style>
:root{
  --gold:#e8c14b;
  --gold-deep:#c99e2a;
  --navy:#141b29;
  --navy-2:#1d2638;
  --ink:#1b1b1b;
  --mist:#dde2ea;
  --white:#ffffff;
  --muted:#5b5f66;
}
*{margin:0;padding:0;box-sizing:border-box}
html,body{width:1200px;height:4240px;overflow:hidden}
body{font-family:"Poppins",sans-serif;color:var(--ink);background:var(--white);position:relative}
.serif{font-family:"Cinzel",serif}
section,header,footer{position:absolute;left:0;width:1200px}
.btn{display:inline-flex;align-items:center;gap:10px;background:var(--gold);color:var(--ink);font-weight:600;font-size:15px;letter-spacing:.5px;padding:0 26px;height:58px;border-radius:4px}
.btn svg{width:18px;height:18px}

/* hero */
.hero{top:0;height:760px;background:linear-gradient(100deg,#0d1119 0%,#1d2230 40%,#2a2f3c 60%,#0c0f16 100%);overflow:hidden}
.hero-photo{position:absolute;inset:0;background:radial-gradient(ellipse at 70% 70%,#3b4150 0%,rgba(20,24,34,.2) 55%,transparent 80%)}
.logo{position:absolute;display:flex;align-items:center;gap:10px;font-family:"Cinzel",serif;font-weight:700;color:var(--gold);letter-spacing:.5px}
.hero .logo{left:100px;top:34px;font-size:26px}
.nav{position:absolute;top:40px;left:420px;display:flex;gap:42px;font-size:17px;color:var(--white)}
.nav a{color:inherit;text-decoration:none}
.nav .active{border-bottom:2px solid var(--white);padding-bottom:4px}
.hero h1{position:absolute;left:120px;top:230px;font-family:"Cinzel",serif;font-weight:400;font-size:70px;line-height:84px;color:var(--white);letter-spacing:2px}
.hero p{position:absolute;left:120px;top:392px;color:var(--white);font-size:22px;line-height:32px}
.hero .btn{position:absolute;left:120px;top:450px}
.hero-wave{position:absolute;left:0;bottom:0;width:1200px;height:140px}

/* about */
.about{top:760px;height:600px}
.about-photo{position:absolute;left:90px;top:70px;width:470px;height:470px;border-radius:40px 0 40px 0;background:linear-gradient(135deg,#f1e2c3,#b89366 55%,#3d3227)}
.about-frame{position:absolute;left:70px;top:50px;width:160px;height:160px;border-top:14px solid var(--gold);border-left:14px solid var(--gold);border-radius:40px 0 0 0}
.about h2{position:absolute;left:610px;top:70px;font-family:"Cinzel",serif;font-size:58px;font-weight:400;letter-spacing:2px}
.about h2 b,.title b{font-weight:700}
.about .copy{position:absolute;left:610px;top:160px;width:540px;font-size:19px;line-height:33px;color:var(--ink)}
.about .copy p+p{margin-top:32px}
.about .btn{position:absolute;left:620px;top:440px}
.about-curve{position:absolute;left:0;top:540px;width:1200px;height:80px}

/* cars */
.cars{top:1350px;height:630px;background:var(--mist)}
.title{font-family:"Cinzel",serif;font-weight:400;font-size:54px;letter-spacing:2px;text-align:center}
.cars .title{position:absolute;top:100px;width:100%}
.car-card{position:absolute;top:200px;width:290px;height:270px;border-radius:44px 0 44px 0;overflow:hidden}
.car-card .shot{position:absolute;inset:0}
.car-card span{position:absolute;left:26px;bottom:30px;color:var(--white);font-weight:600;font-size:20px;line-height:26px}
.dots{position:absolute;top:540px;left:540px;display:flex;gap:14px}
.dots i{display:block;width:36px;height:5px;background:var(--ink);opacity:.35}
.dots i.on{opacity:1}

/* fleet */
.fleet{top:1980px;height:600px;background:var(--navy);overflow:hidden}
.fleet-photo{position:absolute;right:0;top:0;width:760px;height:600px;background:linear-gradient(90deg,var(--navy) 0%,#2c3342 30%,#4a505c 60%,#222834 100%)}
.fleet h2{position:absolute;left:130px;top:150px;font-family:"Cinzel",serif;font-size:56px;color:var(--white);font-weight:600;letter-spacing:2px}
.fleet p{position:absolute;left:130px;top:240px;width:560px;color:var(--white);font-size:19px;line-height:33px}
.fleet .btn{position:absolute;left:130px;top:400px}

/* services */
.services{top:2580px;height:610px}
.services .title{position:absolute;top:80px;width:100%}
.service{position:absolute;top:190px;width:310px;height:310px;border-radius:50%;border:3px solid var(--gold);box-shadow:0 10px 30px rgba(0,0,0,.08);background:var(--white)}
.service .icon{position:absolute;left:105px;top:55px;width:100px;height:100px;border-radius:50%;background:linear-gradient(135deg,#f2d77a,var(--gold-deep))}
.service h3{position:absolute;top:200px;width:100%;text-align:center;font-family:"Cinzel",serif;font-size:26px;font-weight:700}

/* reviews */
.reviews{top:3190px;height:660px;background:linear-gradient(135deg,#f0cc52,#e2b93c 50%,#f3d468);overflow:hidden}
.reviews .title{position:absolute;top:60px;width:100%}
.review{position:absolute;top:200px;width:420px;height:240px;background:var(--white);border-radius:16px;padding:28px 34px;text-align:center}
.stars{display:flex;justify-content:center;gap:6px;margin-bottom:16px}
.stars svg{width:22px;height:22px;fill:var(--gold-deep)}
.review p{font-size:15px;line-height:25px;color:var(--muted)}
.review cite{display:block;margin-top:18px;font-style:normal;font-weight:600;font-size:15px}
.arrow{position:absolute;top:300px;width:40px;height:40px}

/* footer */
.footer{top:3850px;height:390px;background:var(--navy)}
.footer .logo{left:140px;top:50px;font-size:26px}
.socials{position:absolute;left:190px;top:140px;display:flex;gap:18px}
.socials i{display:block;width:24px;height:24px;border-radius:50%;background:var(--gold)}
.cols{position:absolute;left:460px;top:40px;display:flex;gap:80px}
.col h4{color:var(--gold);font-weight:500;font-size:17px;letter-spacing:1px;text-transform:uppercase;margin-bottom:12px}
.col li{list-style:none;color:#cfd3da;font-size:15px;line-height:27px}
.copyright{position:absolute;left:0;bottom:24px;width:100%;text-align:center;color:#8e95a1;font-size:13px}
</style>
</head>
<body>

<header class="hero">
  <div class="hero-photo" role="img" aria-label="Black luxury limousine parked in front of an elegant building at dusk"></div>
  <div class="logo">WestaKolory.pl</div>
  <nav class="nav">
    <a class="active">Home</a><a>About Us</a><a>Fleet</a><a>Cars</a><a>Services</a><a>Why Us</a><a>FAQ</a><a>Contact</a>
  </nav>
  <h1>Luxury<br>Car Wedding</h1>
  <p>Rent a Limousine or a Premium-class<br>Van with a chauffeur</p>
  <a class="btn">EXPLORE CARS <svg viewBox="0 0 20 20"><path d="M3 10h13M11 5l5 5-5 5" stroke="currentColor" stroke-width="2" fill="none"/></svg></a>
  <svg class="hero-wave" viewBox="0 0 1200 140" preserveAspectRatio="none">
    <path d="M0 90 C350 20 750 150 1200 40 L1200 140 L0 140Z" fill="#ffffff"/>
    <path d="M0 80 C350 10 750 140 1200 30" stroke="#e8c14b" stroke-width="10" fill="none"/>
  </svg>
</header>

<section class="about">
  <div class="about-frame"></div>
  <div class="about-photo" role="img" aria-label="Bride in a white gown stepping out of a black car"></div>
  <h2>About <b>Us</b></h2>
  <div class="copy">
    <p>Make your big day truly unforgettable with effortless, elegant transfers anywhere in Poland. At WestaKolory, our professional drivers are friendly, punctual, and ready to customize every detail to your wedding vision.</p>
    <p>From the moment we pick you up to your grand exit, ride in comfort and style—leaving you free to focus on the memories that matter.</p>
  </div>
  <a class="btn">LEARN MORE <svg viewBox="0 0 20 20"><path d="M3 10h13M11 5l5 5-5 5" stroke="currentColor" stroke-width="2" fill="none"/></svg></a>
  <svg class="about-curve" viewBox="0 0 1200 80" preserveAspectRatio="none">
    <path d="M0 20 C400 90 800 70 1200 0" stroke="#e8c14b" stroke-width="6" fill="none"/>
  </svg>
</section>

<section class="cars">
  <h2 class="title">Our <b>Cars</b></h2>
  <div class="car-card" style="left:100px"><div class="shot" role="img" aria-label="Silver premium sedan parked outdoors" style="background:linear-gradient(160deg,#9ea4ac,#4a4f58 60%,#1c1f25)"></div><span>Luxurious<br>Premium Car</span></div>
  <div class="car-card" style="left:420px"><div class="shot" role="img" aria-label="White limousine on a city street" style="background:linear-gradient(160deg,#c9ced6,#6b7280 60%,#23262d)"></div><span>Elegance with<br>Limousine</span></div>
  <div class="car-card" style="left:740px"><div class="shot" role="img" aria-label="Black premium vans lined up" style="background:linear-gradient(160deg,#8b8f96,#3b3f47 60%,#15171b)"></div><span>Premium Vans</span></div>
  <div class="car-card" style="left:1060px"><div class="shot" role="img" aria-label="Luxury sports car" style="background:linear-gradient(160deg,#a9adb4,#55595f 60%,#1c1e22)"></div><span>Luxury Sports</span></div>
  <div class="dots"><i></i><i class="on"></i><i></i></div>
</section>

<section class="fleet">
  <div class="fleet-photo" role="img" aria-label="Chauffeur opening the door of a black luxury sedan"></div>
  <h2>Fleet</h2>
  <p>Make your big day truly unforgettable with effortless, elegant transfers anywhere in Poland. At WestaKolory, our professional drivers are friendly, punctual, and ready to customize every detail to your wedding vision.</p>
  <a class="btn">LEARN MORE <svg viewBox="0 0 20 20"><path d="M3 10h13M11 5l5 5-5 5" stroke="currentColor" stroke-width="2" fill="none"/></svg></a>
</section>

<section class="services">
  <h2 class="title">Our <b>Services</b></h2>
  <div class="service" style="left:135px"><div class="icon" role="img" aria-label="Wedding couple icon"></div><h3>Weddings</h3></div>
  <div class="service" style="left:445px"><div class="icon" role="img" aria-label="Camera on tripod icon"></div><h3>Photo Shoot</h3></div>
  <div class="service" style="left:755px"><div class="icon" role="img" aria-label="Film camera icon"></div><h3>Film Rentals</h3></div>
</section>

<section class="reviews" role="img" aria-label="Gold-tinted photo of a luxury car interior behind the testimonials">
  <h2 class="title">What <b>People Says</b></h2>
  <svg class="arrow" style="left:40px" viewBox="0 0 40 40"><path d="M26 8 14 20l12 12" stroke="#1b1b1b" stroke-width="5" fill="none"/></svg>
  <div class="review" style="left:160px">
    <div class="stars"><svg viewBox="0 0 24 24"><path d="M12 2l3 7 7 .6-5.4 4.7 1.7 7L12 17.6 5.7 21.3l1.7-7L2 9.6 9 9z"/></svg><svg viewBox="0 0 24 24"><path d="M12 2l3 7 7 .6-5.4 4.7 1.7 7L12 17.6 5.7 21.3l1.7-7L2 9.6 9 9z"/></svg><svg viewBox="0 0 24 24"><path d="M12 2l3 7 7 .6-5.4 4.7 1.7 7L12 17.6 5.7 21.3l1.7-7L2 9.6 9 9z"/></svg><svg viewBox="0 0 24 24"><path d="M12 2l3 7 7 .6-5.4 4.7 1.7 7L12 17.6 5.7 21.3l1.7-7L2 9.6 9 9z"/></svg><svg viewBox="0 0 24 24"><path d="M12 2l3 7 7 .6-5.4 4.7 1.7 7L12 17.6 5.7 21.3l1.7-7L2 9.6 9 9z"/></svg></div>
    <p>Veldane is just on another level. We felt like royalty, no joke. Our reception was near Myślenice and the ride there was next level comfort. Smelled like leather and money inside.</p>
    <cite>— Ilona &amp; Tomasz, Myślenice</cite>
  </div>
  <div class="review" style="left:640px">
    <div class="stars"><svg viewBox="0 0 24 24"><path d="M12 2l3 7 7 .6-5.4 4.7 1.7 7L12 17.6 5.7 21.3l1.7-7L2 9.6 9 9z"/></svg><svg viewBox="0 0 24 24"><path d="M12 2l3 7 7 .6-5.4 4.7 1.7 7L12 17.6 5.7 21.3l1.7-7L2 9.6 9 9z"/></svg><svg viewBox="0 0 24 24"><path d="M12 2l3 7 7 .6-5.4 4.7 1.7 7L12 17.6 5.7 21.3l1.7-7L2 9.6 9 9z"/></svg><svg viewBox="0 0 24 24"><path d="M12 2l3 7 7 .6-5.4 4.7 1.7 7L12 17.6 5.7 21.3l1.7-7L2 9.6 9 9z"/></svg><svg viewBox="0 0 24 24"><path d="M12 2l3 7 7 .6-5.4 4.7 1.7 7L12 17.6 5.7 21.3l1.7-7L2 9.6 9 9z"/></svg></div>
    <p>Ostrava GT sounds like a beast but looks like a million bucks. We took it for our civil wedding at the town hall in Kraków and literally everyone turned their heads. Pure class.</p>
    <cite>— Dorota K., Kraków</cite>
  </div>
  <svg class="arrow" style="left:1120px" viewBox="0 0 40 40"><path d="M14 8l12 12-12 12" stroke="#1b1b1b" stroke-width="5" fill="none"/></svg>
</section>

<footer class="footer">
  <div class="logo">WestaKolory.pl</div>
  <div class="socials"><i></i><i></i></div>
  <div class="cols">
    <div class="col"><h4>Quick Links</h4><ul><li>About Us</li><li>Blog</li><li>FAQ</li><li>Privacy Policy</li><li>Terms &amp; Conditions</li></ul></div>
    <div class="col"><h4>Resources</h4><ul><li>Login</li><li>Order History</li><li>Affiliates</li><li>Newsletter</li><li>Gift Certificat</li></ul></div>
    <div class="col"><h4>Customer Service</h4><ul><li>Contact Us</li><li>Store Locations</li><li>Our Brands</li><li>Site Map</li><li>Delivery Information</li></ul></div>
  </div>
  <div class="copyright">Copyright © 2025 WestaKolory.pl All rights reserved.</div>
</footer>

</body>
</html>
```